Local Roofing/Construction company business needs new biz card design

We need a new business card design, current cards are from the start of this operation and generic at best. We are a local Construction Company (General Contractor) with a majority of our work originating from insurance claims-exterior finish work is the main focus (Roofs-Siding-Gutters etc). Heavily involved with homeowners and the low ball offers they receive from insurance company's after a insurable event takes place. I have attached some of our original logo file(s) below.

```html
<!DOCTYPE html>
<html lang="en">
<head>
<meta charset="UTF-8">
<title>Ridgeline Construction – Business Card</title>
<link href="https://fonts.googleapis.com/css2?family=Montserrat:wght@400;500;700;800&display=swap" rel="stylesheet">
<style>
  :root {
    --page-bg: #1b1d1f;
    --card-bg: #0f1d20;
    --pattern-a: #14272b;
    --pattern-b: #1a3337;
    --accent: #55b96a;
    --text-light: #f2f4f3;
  }
  * { box-sizing: border-box; margin: 0; padding: 0; }
  html, body {
    width: 1200px; height: 900px; overflow: hidden;
    background: var(--page-bg);
    font-family: "Montserrat", sans-serif;
  }
  .sheet {
    width: 1200px; height: 900px;
    display: flex; flex-direction: column; align-items: center; justify-content: center;
    gap: 50px;
  }
  .card {
    position: relative;
    width: 630px; height: 360px;
    border-radius: 18px;
    background: var(--card-bg);
    overflow: hidden;
  }
  /* Front */
  .card-front .accent-band {
    position: absolute; left: 0; right: 0; bottom: 0; height: 12px;
    background: var(--accent);
  }
  .brand-name {
    position: absolute; top: 52px; right: 44px;
    display: flex; align-items: center; gap: 12px;
    color: var(--accent);
    font-weight: 800; font-size: 30px; letter-spacing: 1px;
    text-transform: uppercase;
  }
  .brand-name .brand-square {
    width: 22px; height: 22px; background: var(--accent);
  }
  .person {
    position: absolute; left: 44px; top: 150px;
  }
  .person-name {
    color: var(--accent); font-weight: 700; font-size: 24px;
    letter-spacing: 1.5px; text-transform: uppercase;
  }
  .person-title {
    color: var(--text-light); font-weight: 400; font-size: 14px;
    margin-top: 6px; padding-left: 70px; letter-spacing: 0.5px;
  }
  .divider {
    position: absolute; left: 318px; top: 150px;
    width: 1.5px; height: 82px; background: var(--accent);
  }
  .contacts {
    position: absolute; left: 338px; top: 152px;
    list-style: none;
    color: var(--text-light); font-size: 14px; font-weight: 500;
  }
  .contacts li { display: flex; align-items: center; gap: 9px; height: 26px; }
  .contacts svg { width: 13px; height: 13px; fill: var(--accent); flex: none; }
  .address {
    position: absolute; left: 44px; bottom: 50px;
    color: var(--text-light); font-size: 14px; font-weight: 500; letter-spacing: 0.3px;
  }
  /* Back */
  .card-back .pattern-fill {
    position: absolute; inset: 0;
    background: linear-gradient(135deg, var(--pattern-a), var(--pattern-b) 55%, var(--pattern-a));
  }
  .back-brand {
    position: absolute; left: 36px; bottom: 30px;
    display: flex; align-items: center; gap: 8px;
    color: var(--accent); font-weight: 800; font-size: 15px;
    text-transform: uppercase; letter-spacing: 0.5px;
  }
  .back-brand .brand-square { width: 12px; height: 12px; background: var(--accent); }
</style>
</head>
<body>
<main class="sheet">
  <section class="card card-front" aria-label="Card front">
    <div class="brand-name"><span class="brand-square"></span>Ridgeline Construction</div>

    <div class="person">
      <p class="person-name">Marcus Hollis</p>
      <p class="person-title">Managing Director</p>
    </div>

    <div class="divider"></div>

    <ul class="contacts">
      <li>
        <svg viewBox="0 0 24 24"><path d="M6.6 10.8a15.1 15.1 0 0 0 6.6 6.6l2.2-2.2a1 1 0 0 1 1-.25 11.4 11.4 0 0 0 3.6.57 1 1 0 0 1 1 1V20a1 1 0 0 1-1 1A17 17 0 0 1 3 4a1 1 0 0 1 1-1h3.5a1 1 0 0 1 1 1c0 1.25.2 2.45.57 3.57a1 1 0 0 1-.25 1z"/></svg>
        0412 555 019
      </li>
      <li>
        <svg viewBox="0 0 24 24"><path d="M2 5h20v14H2zm2 2v.5l8 5 8-5V7zm0 2.9V17h16V9.9l-8 5z"/></svg>
        info@ridgelinebuild.com
      </li>
      <li>
        <svg viewBox="0 0 24 24"><path d="M12 2a10 10 0 1 0 0 20 10 10 0 0 0 0-20zm6.9 6h-3a15.6 15.6 0 0 0-1.3-3.9A8 8 0 0 1 18.9 8zM12 4.1A13.8 13.8 0 0 1 13.8 8h-3.6A13.8 13.8 0 0 1 12 4.1zM4.3 14a8 8 0 0 1 0-4h3.4a16 16 0 0 0 0 4zm.8 2h3a15.6 15.6 0 0 0 1.3 3.9A8 8 0 0 1 5.1 16zm3-8h-3a8 8 0 0 1 4.3-3.9A15.6 15.6 0 0 0 8.1 8zM12 19.9A13.8 13.8 0 0 1 10.2 16h3.6a13.8 13.8 0 0 1-1.8 3.9zm2.2-5.9H9.8a14 14 0 0 1 0-4h4.4a14 14 0 0 1 0 4zm.4 5.9a15.6 15.6 0 0 0 1.3-3.9h3a8 8 0 0 1-4.3 3.9zM16.3 14a16 16 0 0 0 0-4h3.4a8 8 0 0 1 0 4z"/></svg>
        www.ridgelinebuild.com
      </li>
    </ul>

    <p class="address">118 W Harlow Street Dalton County Name 5204</p>
    <div class="accent-band"></div>
  </section>

  <section class="card card-back" aria-label="Card back">
    <div class="pattern-fill" role="img" aria-label="Repeating tonal pattern of the company mark across the card back"></div>
    <div class="back-brand"><span class="brand-square"></span>Ridgeline</div>
  </section>
</main>
</body>
</html>
```